VL - menu design

Hi,

We require elegant menu design for upscale restaurant. Please find attached the logo and the menu items for your reference.

for inspiration, this is a good website: -
http://www.plateworthy-sample.net/dishcraft/about.php

We are very much open for Menu Size suggestions.

unfortunately the place is going under renovation, we don't have updated images to it. the closest look and feel to our place is http://vazelo-example.com ..

we are also open for creative options on the shape, the styles, etc. as long as it represents the fine dine feel ...

Thanks ...

Dear All,

We wouldlike to extend our apology for not being able to provide feedbacks on everysingle design. We were extremely busy and we have multiple contests opensimultaneously which makes the process even harder.

However,we would like to thank you all for the efforts you have put into designingour menu. It is very much appreciated …

We wishyou all success in your design ventures and we are quite positive that we willbe working with many of you on many projects in the soon future. 

Thanks & Regards,

DQI Team...

 

 

 

Industry/Entity Type

Restaurant

Requirements
Must have
• Please ensure that there are 'some' images in the menu ... this is very important.
Should not have
• IMPORTANT: -

1. Please DO NOT insert any currency sign to the menu
2. Please keep the prices of the menu at the end of the menu items descriptions NOT beside the menu item names. The font of the price should be similar to the menu item description and please DO NOT bold the numbers. the prices should be subtle.

Thank you ...

```html
<!DOCTYPE html>
<html lang="en">
<head>
<meta charset="utf-8">
<title>Linden Row Café – Beverage Menu</title>
<link rel="stylesheet" href="https://fonts.googleapis.com/css2?family=Crimson+Text:ital,wght@0,600;0,700;1,400;1,600;1,700&family=Raleway:wght@300;400&display=swap">
<style>
:root{
  --paper:#ffffff;
  --ink:#1e1e1e;
  --heading:#5a5a5a;
  --accent:#a0845f;
  --rule:#b9b9b9;
  --art-light:#ece6dc;
  --art-mid:#cbbda8;
}
*{margin:0;padding:0;box-sizing:border-box}
html,body{width:1200px;height:1200px;overflow:hidden;background:var(--paper)}
.menu{position:relative;width:1200px;height:1200px;background:var(--paper);color:var(--ink);font-family:"Crimson Text",Georgia,serif}

.brand{position:absolute;left:95px;top:85px;display:flex;align-items:center;gap:14px}
.brand-mark{width:16px;height:16px;background:var(--ink)}
.brand-name{font-family:"Raleway",Arial,sans-serif;font-weight:400;font-size:40px;letter-spacing:6px;color:var(--ink);line-height:1}

.section-title{position:absolute;font-family:"Raleway",Arial,sans-serif;font-weight:300;font-size:36px;letter-spacing:1px;color:var(--heading);line-height:1;text-align:center}
.rule{position:absolute;border-top:1px dotted var(--rule)}
.rule-v{position:absolute;border-left:1px dotted var(--rule)}

.group{position:absolute}
.group-title{font-weight:700;font-size:20px;color:var(--accent);letter-spacing:.5px;line-height:31px;margin-bottom:1px}
.item{font-style:italic;font-weight:700;font-size:16.5px;line-height:31.2px;white-space:nowrap}
.item .price{font-weight:400}
.item-note{font-style:italic;font-weight:400;font-size:14.5px;line-height:23px;margin-top:-5px;margin-bottom:3px}

.art{position:absolute}
.art-bottle{left:520px;top:548px;width:185px;height:272px;background:linear-gradient(160deg,var(--art-light),var(--art-mid));border-radius:40px 40px 8px 8px}
.art-beans{left:33px;top:1008px;width:234px;height:108px;background:linear-gradient(90deg,var(--art-mid),var(--art-light));border-radius:50px}

.cocktails{position:absolute;left:745px;top:75px;width:408px;height:1087px;border:1px dotted var(--rule)}
.cocktails::before{content:"";position:absolute;inset:8px;border:1px dotted var(--rule)}
.cocktails .section-title{left:0;right:0;top:50px}
.cocktail{position:absolute;left:20px;right:20px;text-align:center}
.cocktail-name{font-weight:700;font-size:20px;color:var(--accent);line-height:26px}
.cocktail-desc{font-style:italic;font-size:14.5px;line-height:21px}
</style>
</head>
<body>
<main class="menu">

  <header class="brand">
    <span class="brand-mark"></span>
    <span class="brand-name">LINDEN ROW CAFÉ</span>
  </header>

  <div class="rule" style="left:75px;top:250px;width:628px"></div>
  <h2 class="section-title" style="left:75px;width:628px;top:258px">COLD BEVERAGES</h2>
  <div class="rule" style="left:75px;top:302px;width:628px"></div>

  <section class="group" style="left:78px;top:313px">
    <h3 class="group-title">ICE TEAS</h3>
    <p class="item">Peach Ice Tea. <span class="price">30</span></p>
    <p class="item">Lemon Ice Tea. <span class="price">30</span></p>
    <p class="item">Mint Ice Tea. <span class="price">30</span></p>
    <p class="item">Water / Soda</p>
    <p class="item">Corva. <span class="price">20</span></p>
    <p class="item">Diet Corva. <span class="price">20</span></p>
    <p class="item">Limara. <span class="price">20</span></p>
    <p class="item">Diet Limara. <span class="price">20</span></p>
    <p class="item">Ginger Ale. <span class="price">20</span></p>
    <p class="item">Orvella. <span class="price">20</span></p>
    <p class="item">Taurex. <span class="price">45</span></p>
    <p class="item">Belmonte 330cl. <span class="price">20</span></p>
    <p class="item">Belmonte 750cl. <span class="price">30</span></p>
    <p class="item">Alpessa 330cl. <span class="price">20</span></p>
    <p class="item">Alpessa 750cl. <span class="price">30</span></p>
  </section>

  <section class="group" style="left:267px;top:313px">
    <h3 class="group-title">MILK SHAKES</h3>
    <p class="item">Milk Shake Linden</p>
    <p class="item-note">Vanilla Ice cream, Fresh Pinapple,<br>Dates, Banana, Lemone Juice. 36</p>
    <p class="item">Strawberry Milk Shake <span class="price">33</span></p>
    <p class="item">Vanilla Milk Shake <span class="price">33</span></p>
    <p class="item">Chocolate Milk Shake <span class="price">33</span></p>
  </section>

  <section class="group" style="left:267px;top:530px">
    <h3 class="group-title">JUICES</h3>
    <p class="item">Fresh Orange Juice. <span class="price">35</span></p>
    <p class="item">Fresh Lemon Juice. <span class="price">35</span></p>
    <p class="item">Fresh Pineapple Juice. <span class="price">35</span></p>
    <p class="item">Fresh Watermelon. <span class="price">35</span></p>
    <p class="item">Fresh Mango Juice. <span class="price">35</span></p>
    <p class="item">Carrot juice. <span class="price">35</span></p>
    <p class="item">Fresh Strawberry Juice. <span class="price">35</span></p>
    <p class="item">Green Apple Juice. <span class="price">35</span></p>
  </section>

  <section class="group" style="left:525px;top:313px">
    <h3 class="group-title">ICE COFFEE</h3>
    <p class="item">Ice Cappuccino. <span class="price">30</span></p>
    <p class="item">Ice Coffee. <span class="price">30</span></p>
    <p class="item">Ice Mocha .<span class="price">30</span></p>
    <p class="item">Espresso Freddo. <span class="price">24</span></p>
    <p class="item">Shakerato. <span class="price">24</span></p>
    <p class="item">Frappe Al Coffee. <span class="price">24</span></p>
  </section>

  <div class="art art-bottle" role="img" aria-label="Sketch of a bottle and a glass"></div>

  <div class="rule" style="left:75px;top:843px;width:425px"></div>
  <div class="rule" style="left:508px;top:843px;width:195px"></div>
  <div class="rule-v" style="left:503px;top:843px;height:265px"></div>
  <h2 class="section-title" style="left:75px;width:425px;top:853px">COFFEE</h2>
  <h2 class="section-title" style="left:508px;width:195px;top:853px">HOT TEA</h2>
  <div class="rule" style="left:75px;top:897px;width:425px"></div>

  <section class="group" style="left:78px;top:897px">
    <p class="item">Coffee Americano. <span class="price">30</span></p>
    <p class="item">Cappuccino. <span class="price">35</span></p>
    <p class="item">Latte Macchiato. <span class="price">35</span></p>
  </section>

  <section class="group" style="left:267px;top:897px">
    <p class="item">Espresso. <span class="price">24</span></p>
    <p class="item">Espresso Doppio. <span class="price">35</span></p>
    <p class="item">Espresso Decaffeinato. <span class="price">23</span></p>
    <p class="item">Mocka Roma. <span class="price">39</span></p>
    <p class="item">Cappuccino Viennese. <span class="price">39</span></p>
    <p class="item">Hot Chocolate. <span class="price">35</span></p>
    <p class="item">Turkish coffee. <span class="price">25</span></p>
  </section>

  <section class="group" style="left:528px;top:897px">
    <p class="item">English breakfast. <span class="price">35</span></p>
    <p class="item">Pure Green tea <span class="price">35</span></p>
    <p class="item">Earl Gray. <span class="price">35</span></p>
    <p class="item">Jasmine. <span class="price">35</span></p>
    <p class="item">Mint. <span class="price">35</span></p>
    <p class="item">Peppermint. <span class="price">35</span></p>
    <p class="item">Herbal. <span class="price">35</span></p>
  </section>

  <div class="art art-beans" role="img" aria-label="Sketch of coffee beans"></div>

  <aside class="cocktails">
    <h2 class="section-title">COCKTAILS</h2>

    <div class="cocktail" style="top:92px">
      <h3 class="cocktail-name">Lemon with Mint</h3>
      <p class="cocktail-desc">Lemon Juice, Sugar Syrup, Fresh Mint. 35</p>
    </div>
    <div class="cocktail" style="top:150px">
      <h3 class="cocktail-name">Virgin Passion</h3>
      <p class="cocktail-desc">Fresh Passion Fruit, Litchi Juice,<br>Rose and Vanilla Syrup. 35</p>
    </div>
    <div class="cocktail" style="top:226px">
      <h3 class="cocktail-name">Afogatto</h3>
      <p class="cocktail-desc">Scoop of Vanilla Ice cream<br>topped with one espresso shot. 35</p>
    </div>
    <div class="cocktail" style="top:305px">
      <h3 class="cocktail-name">Very Berry</h3>
      <p class="cocktail-desc">Mixed Berries, Cranberry<br>And lemon Juice, Vanilla twist. 35</p>
    </div>
    <div class="cocktail" style="top:383px">
      <h3 class="cocktail-name">Blue Lemonade</h3>
      <p class="cocktail-desc">Fresh lemon juice, Wild mint and blue lagoon<br>syrup topped with Limara .35</p>
    </div>
    <div class="cocktail" style="top:460px">
      <h3 class="cocktail-name">Linden Island</h3>
      <p class="cocktail-desc">Apple, Pineapple and strawberry Juice<br>topped with almond Syrup. 35</p>
    </div>
    <div class="cocktail" style="top:538px">
      <h3 class="cocktail-name">Rosso di Serra</h3>
      <p class="cocktail-desc">Fresh Passion Fruit, Cranberry Juice and ginger<br>ale topped with grenadine Syrup. 35</p>
    </div>
    <div class="cocktail" style="top:617px">
      <h3 class="cocktail-name">Bomb</h3>
      <p class="cocktail-desc">Apple Juice, Orange Juice, Taurex<br>Toped with Amaretto Syrup. 39</p>
    </div>
    <div class="cocktail" style="top:695px">
      <h3 class="cocktail-name">Virgin Mojito</h3>
      <p class="cocktail-desc">Fresh Mint leaves, Apple Juice shaked<br>with fresh lemon Juice. 35</p>
    </div>
    <div class="cocktail" style="top:775px">
      <h3 class="cocktail-name">Raspberry Spritzer</h3>
      <p class="cocktail-desc">Fresh Raspberry, Cranberry juice, Raspberry<br>syrup and grenadine topped with soda water. 35</p>
    </div>
    <div class="cocktail" style="top:850px">
      <h3 class="cocktail-name">Pinacolada</h3>
      <p class="cocktail-desc">Vanilla Ice cream, Fresh pineapple Juice and<br>coco Marlena topped with almond Syrup. 35</p>
    </div>
    <div class="cocktail" style="top:928px">
      <h3 class="cocktail-name">Linden Row</h3>
      <p class="cocktail-desc">Fresh Pineapple Juice, Fresh Orange Juice and<br>passion fruit, Topped with a hint of Vanilla. 35</p>
    </div>
  </aside>

</main>
</body>
</html>
```